Glimmer Step Blog

Need a blog design. I am the first fashion dance blogger-very exciting! My first project will be reporting on Twirling Under Lanterns which premieres this Monday-St. Patrick's Day. I am looking for an exciting format to represent my new venture. I will be focusing on ballroom dance fashion-I like creativity and look for something with a cool color scheme, artistic, could be modern or really open for someone to interpret this concept in a creative way. The blog name is GlimStep.

Fashion

```html
<!DOCTYPE html>
<html lang="en">
<head>
<meta charset="utf-8">
<title>GlimStep</title>
<link href="https://fonts.googleapis.com/css2?family=Questrial&family=Open+Sans:ital,wght@0,400;0,600;0,700;1,400&family=Great+Vibes&display=swap" rel="stylesheet">
<style>
:root{
  --ink:#3d2b13;
  --nav:#3a2910;
  --nav-active:#2c1f0b;
  --nav-text:#cbb58a;
  --gold:#8a6c3c;
  --panel:#85693f;
  --text:#333;
  --muted:#888;
  --line:#e2e2e2;
  --footer:#1f1f1f;
}
*{box-sizing:border-box;margin:0;padding:0}
html,body{width:1200px;height:2353px;overflow:hidden;background:#fff}
body{position:relative;font-family:"Open Sans",Arial,sans-serif;color:var(--text)}
.abs{position:absolute}
.header{left:0;top:0;width:1200px;height:438px;background:#fff}
.hero-photo{left:500px;top:0;width:580px;height:438px;background:linear-gradient(90deg,#fff 0%,#f2f2f2 30%,#e4e4e4 50%,#f2f2f2 70%,#fff 100%)}
.brand{left:185px;top:108px;font-family:"Questrial",sans-serif;font-size:56px;color:var(--ink);font-weight:400;letter-spacing:.5px}
.tagline{left:185px;top:178px;font-size:26px;line-height:34px;color:#1c1c1c}
.byline{left:300px;top:270px;width:172px;text-align:right;font-style:italic;font-size:17px;color:#777}
.byline:before{content:"";display:block;margin-left:148px;width:24px;border-top:1px dotted #999;margin-bottom:6px}
.dropdown{left:289px;top:330px;width:124px;height:98px;border:1px solid #ddd;background:#fff;box-shadow:0 1px 3px rgba(0,0,0,.08);padding:14px 0 0 19px;font-size:12.5px;line-height:22px;color:#888;list-style:none;white-space:nowrap}
.dropdown:after{content:"";position:absolute;left:55px;bottom:-7px;width:12px;height:12px;background:#fff;border-right:1px solid #ddd;border-bottom:1px solid #ddd;transform:rotate(45deg)}
.nav{left:0;top:438px;width:1200px;height:52px;background:var(--nav);border-bottom:1px solid #000}
.nav ul{list-style:none;position:absolute;left:170px;top:0;display:flex;height:52px}
.nav li{font-family:"Questrial",sans-serif;font-weight:700;font-size:18px;color:var(--nav-text);padding:0 17px;line-height:52px}
.nav li.active{background:var(--nav-active);color:#fff;border-left:1px solid #4a381c;border-right:1px solid #4a381c}
.social{display:flex;gap:9px}
.social span{display:block;width:18px;height:18px;border-radius:50%;background:#d8cfc0}
.nav .social{position:absolute;left:912px;top:17px}
.post{left:185px;width:553px}
.post .photo{position:absolute;left:0;top:0;width:274px;height:192px;border:1px solid #ddd;padding:4px;background:#fff}
.post .photo div{width:100%;height:100%}
.post .body{position:absolute;left:287px;top:0;width:266px}
.meta{font-size:10.5px;color:#555;padding:4px 0 9px 0;border-bottom:1px solid var(--line);display:flex;gap:26px}
.meta .c:before{content:"";display:inline-block;width:9px;height:8px;background:#555;border-radius:50% 50% 50% 0;margin-right:5px}
.post h2{font-family:"Questrial",sans-serif;font-weight:400;font-size:27px;line-height:31px;color:var(--gold);padding:10px 0 8px;border-bottom:1px solid var(--line);margin-bottom:8px}
.post p{font-size:12.5px;line-height:15.5px;color:#222;margin-bottom:14px}
.share{position:absolute;left:0;width:553px;height:33px;border-top:1px solid #eee;border-bottom:1px dashed #ccc;display:flex;align-items:center;gap:6px;font-size:9px;color:#555}
.share .btn{border:1px solid #ccc;border-radius:2px;padding:0 4px;background:#f4f6fa;color:#335}
.share .n{border:1px solid #ddd;padding:0 4px;background:#fff}
.share .more{margin-left:auto;font-size:12.5px;color:#666}
.box{left:773px;width:240px;border:1px solid #ddd;border-radius:2px;background:#fff}
.welcome{background:var(--panel);border:none;padding:26px 27px;color:#fff}
.welcome h3{font-family:"Great Vibes",cursive;font-weight:400;font-size:34px;line-height:44px;margin-bottom:12px}
.welcome p{font-size:12.5px;line-height:18px;color:#f3ead8}
.welcome a{display:block;margin-top:24px;font-size:12.5px;color:#fff}
.box-title{display:flex;align-items:center;gap:10px;margin:28px 18px 0;padding-bottom:12px;border-bottom:1px solid var(--line)}
.box-title .dot{width:34px;height:24px;border-radius:50%;background:var(--gold)}
.box-title b{font-family:"Questrial",sans-serif;font-size:19px;color:var(--ink);display:block}
.box-title small{font-size:10.5px;color:#999}
.feed{list-style:none;padding:10px 18px}
.feed li{display:flex;gap:10px;padding:12px 0 10px;font-size:10.5px;line-height:14px;color:#333}
.thumb{flex:none;width:34px;height:34px;border:1px solid #ddd;padding:2px;background:#fff}
.thumb div{width:100%;height:100%}
.feed em{display:block;color:var(--gold);font-size:9px}
.fb-head{background:var(--panel);height:47px;color:#fff;font-weight:700;font-size:15px;line-height:47px;padding-left:22px}
.fb-page{display:flex;gap:14px;margin:14px 18px 0;padding-bottom:10px;border-bottom:1px solid var(--line)}
.fb-page .mark{font-family:"Questrial",sans-serif;font-size:26px;color:#333;width:40px}
.fb-page b{font-size:11px;color:#3b5998;display:block}
.fb-page i{font-style:normal;font-size:9px;border:1px solid #ccd;padding:0 4px;color:#3b5998}
.fb-count{margin:8px 18px;font-size:9px;color:#333}
.fb-grid{display:grid;grid-template-columns:repeat(4,42px);gap:6px 13px;margin:0 18px;font-size:8.5px;text-align:center;color:#333}
.fb-grid div div{width:42px;height:38px;margin-bottom:3px}
.fb-foot{margin:10px 18px 0;padding-top:6px;border-top:1px solid #eee;font-size:8.5px;color:#333}
.comments h3{font-family:"Questrial",sans-serif;font-weight:700;font-size:21px;color:var(--gold);margin:26px 24px 0;padding-bottom:12px;border-bottom:1px solid var(--line)}
.comments ul{list-style:none;padding:6px 24px}
.comments li{display:flex;gap:12px;padding:14px 0 6px;font-size:11px;line-height:15px;color:#222}
.comments li small{display:block;font-style:italic;color:#888;font-size:9px;margin-top:8px}
.comments .more{text-align:right;padding:8px 26px;font-size:12.5px;color:#666}
.footer{left:0;top:2302px;width:1200px;height:51px;background:var(--footer);color:#ddd;font-size:11px}
.footer span.copy{position:absolute;left:185px;top:17px}
.footer .social{position:absolute;left:912px;top:16px}
.footer .social span{background:#bbb}
</style>
</head>
<body>
<header class="abs header">
  <div class="abs hero-photo" role="img" aria-label="Dancer's legs in silver leggings and heels beside a mirror ball"></div>
  <h1 class="abs brand">GlimStep</h1>
  <p class="abs tagline">Move Your Body to the<br>Beat of Fashion.</p>
  <p class="abs byline">Mara Ellison</p>
  <ul class="abs dropdown"><li>Designers</li><li>Dancers</li><li>Dance Industry</li></ul>
</header>
<nav class="abs nav">
  <ul><li>Television</li><li class="active">Interviews</li><li>Hairpins to Hemlines</li></ul>
  <div class="social"><span></span><span></span><span></span><span></span></div>
</nav>

<article class="abs post" style="top:552px;height:262px">
  <div class="photo"><div role="img" aria-label="Group of dancers posing in party outfits" style="background:linear-gradient(135deg,#8a7ca8,#c9b6b0,#6b5b6e)"></div></div>
  <div class="body"><div class="meta"><span>March 17, 2014,</span><span class="c">5 Comments</span></div>
  <h2>Dolor sit amet, consec tetur adipiscing elit.</h2>
  <p>Lorem ipsum dolor sit amet, consec tetur adipiscing elit. In fermentum dolor non augue pretium egestas. Donec sem eros, tincidunt at congue ut, posuere sit amet est. Vivamus scelerisque...</p></div>
  <div class="share" style="top:229px"><span class="btn">Like</span><span class="n">3k</span><span class="btn">Chirp</span><span class="n">316</span><span class="btn">Plus</span><span class="n">56</span><span class="more">Full Story →</span></div>
</article>

<article class="abs post" style="top:860px;height:309px">
  <div class="photo"><div role="img" aria-label="Dance troupe performing on a dark stage" style="background:linear-gradient(135deg,#111,#3a2a22,#111)"></div></div>
  <div class="body"><div class="meta"><span>March 17, 2014,</span><span class="c">5 Comments</span></div>
  <h2>Dolor sit amet, consec tetur adipiscing elit.</h2>
  <p>Lorem ipsum dolor sit amet, consectetur adipiscing elit. In fermentum dolor non augue pretium egestas. Donec sem eros, tincidunt at congue ut, posuere sit amet est.</p>
  <p>Vivamus scelerisque viverra odio sit amet laoreet. Ut nec neque non justo rutrum tempor lobortis eu ante. Aliquam sagittis, nibh quis commodo auctor</p></div>
  <div class="share" style="top:276px"><span class="btn">Like</span><span class="n">3k</span><span class="btn">Chirp</span><span class="n">316</span><span class="btn">Plus</span><span class="n">56</span><span class="more">Full Story →</span></div>
</article>

<article class="abs post" style="top:1213px;height:309px">
  <div class="photo"><div role="img" aria-label="Dancers in flowing white costumes" style="background:linear-gradient(135deg,#6d7674,#cfcfd6,#7f8886)"></div></div>
  <div class="body"><div class="meta"><span>March 17, 2014,</span><span class="c">5 Comments</span></div>
  <h2>Dolor sit amet, consec tetur adipiscing elit.</h2>
  <p>Lorem ipsum dolor sit amet, consectetur adipiscing elit. In fermentum dolor non augue pretium egestas. Donec sem eros, tincidunt at congue ut, posuere sit amet est. Vivamus scelerisque viverra odio sit amet laoreet. Ut nec neque non justo rutrum tempor lobortis eu ante. Aliquam sagittis, nibh quis commodo auctor&nbsp; tempor lobortis eu ante.</p></div>
  <div class="share" style="top:278px"><span class="btn">Like</span><span class="n">3k</span><span class="btn">Chirp</span><span class="n">316</span><span class="btn">Plus</span><span class="n">56</span><span class="more">Full Story →</span></div>
</article>

<article class="abs post" style="top:1570px;height:305px">
  <div class="photo"><div role="img" aria-label="Ballroom couple in sparkling costumes" style="background:linear-gradient(135deg,#1a0d0a,#8a4a3a,#2a1510)"></div></div>
  <div class="body"><div class="meta"><span>March 17, 2014,</span><span class="c">5 Comments</span></div>
  <h2>Dolor sit amet, consec tetur adipiscing elit.</h2>
  <p>Lorem ipsum dolor sit amet, consectetur adipiscing elit. In fermentum dolor non augue pretium egestas. Donec sem eros, tincidunt at congue ut, posuere sit amet est.</p>
  <p>Vivamus scelerisque viverra odio sit amet laoreet. Ut nec neque non justo rutrum tempor lobortis eu ante. Aliquam sagittis, nibh quis commodo auctor</p></div>
  <div class="share" style="top:274px"><span class="btn">Like</span><span class="n">3k</span><span class="btn">Chirp</span><span class="n">316</span><span class="btn">Plus</span><span class="n">56</span><span class="more">Full Story →</span></div>
</article>

<article class="abs post" style="top:1923px;height:308px">
  <div class="photo"><div role="img" aria-label="Ballroom couple dancing, black and white with pink gown" style="background:linear-gradient(135deg,#2a2a2a,#9a9a9a,#c86a8a,#333)"></div></div>
  <div class="body"><div class="meta"><span>March 17, 2014,</span><span class="c">5 Comments</span></div>
  <h2>Dolor sit amet, consec tetur adipiscing elit.</h2>
  <p>Lorem ipsum dolor sit amet, consectetur adipiscing elit. In fermentum dolor non augue pretium egestas. Donec sem eros, tincidunt at congue ut, posuere sit amet est.</p>
  <p>Vivamus scelerisque viverra odio sit amet laoreet. Ut nec neque non justo rutrum tempor lobortis eu ante. Aliquam sagittis, nibh quis commodo auctor</p></div>
  <div class="share" style="top:274px;border-bottom:none"><span class="btn">Like</span><span class="n">3k</span><span class="btn">Chirp</span><span class="n">316</span><span class="btn">Plus</span><span class="n">56</span><span class="more">Full Story →</span></div>
</article>

<aside>
  <section class="abs box welcome" style="top:552px;height:397px">
    <h3>Welcome to<br>GlimStep</h3>
    <p>Lorem ipsum dolor sit amet, consec tetur adipiscing elit. In fermentum dolor non augue pretium egestas. Donec sem eros, tincidunt at congue ut, posuere sit amet est. Vivamus scelerisque viverra odio sit amet laoreet. Ut nec neque non justo rutrum tempor lobortis eu ante. Aliquam sagittis, nibh quis commodo auctor</p>
    <a>Learn More →</a>
  </section>

  <section class="abs box" style="top:979px;height:442px">
    <div class="box-title"><span class="dot"></span><div><b>Chirper Feed</b><small>Join the Conversation</small></div></div>
    <ul class="feed">
      <li><span class="thumb"><div role="img" aria-label="Avatar" style="background:#d9b98a"></div></span><div>GlimStep, lorem dolor sit amet, elit dolor sit amet... http://glimstep.5fd6z<em>2 hour ago, favourite, reshare</em></div></li>
      <li><span class="thumb"><div role="img" aria-label="Avatar" style="background:#3a2a2a"></div></span><div>GlimStep, lorem dolor sit amet, elit dolor sit amet... http://glimstep.5fd6z<em>2 hour ago, favourite, reshare</em></div></li>
      <li><span class="thumb"><div role="img" aria-label="Avatar" style="background:#2a1a14"></div></span><div>GlimStep, lorem dolor sit amet, elit dolor sit amet... http://glimstep.5fd6z<em>2 hour ago, favourite, reshare</em></div></li>
      <li><span class="thumb"><div role="img" aria-label="Avatar" style="background:#7a3a2a"></div></span><div>GlimStep, lorem dolor sit amet, elit dolor sit amet... http://glimstep.5fd6z<em>2 hour ago, favourite, reshare</em></div></li>
    </ul>
  </section>

  <section class="abs box" style="top:1451px;height:317px">
    <div class="fb-head">Find us on Facepage</div>
    <div class="fb-page"><span class="mark">GS</span><div><b>Glimmer-Step</b><i>Like</i></div></div>
    <p class="fb-count">207 people like <span style="color:#3b5998">Glimmer Step</span></p>
    <div class="fb-grid">
      <div><div role="img" aria-label="Fan avatar" style="background:#b07a4a"></div>Pacifico</div>
      <div><div role="img" aria-label="Fan avatar" style="background:#8a6a2a"></div>Buyers</div>
      <div><div role="img" aria-label="Fan avatar" style="background:#9a8a6a"></div>Peter Doe</div>
      <div><div role="img" aria-label="Fan avatar" style="background:#3a6a5a"></div>James</div>
      <div><div role="img" aria-label="Fan avatar" style="background:#7a2a2a"></div>James</div>
      <div><div role="img" aria-label="Fan avatar" style="background:#3a5a5a"></div>Peter Doe</div>
      <div><div role="img" aria-label="Fan avatar" style="background:#d8b88a"></div>Peter Doe</div>
      <div><div role="img" aria-label="Fan avatar" style="background:#c89a8a"></div>Jolly</div>
    </div>
    <p class="fb-foot">Facepage social plugin</p>
  </section>

  <section class="abs box comments" style="top:1796px;height:421px">
    <h3>Recent Comments</h3>
    <ul>
      <li><span class="thumb"><div role="img" aria-label="Avatar" style="background:#d9b98a"></div></span><div>Lorem ipsum testing tincidu lorem dolor sit amet, elit dolor sitsitnt posuere..<small>Mara Ellison &nbsp; March 17, 2014</small></div></li>
      <li><span class="thumb"><div role="img" aria-label="Avatar" style="background:#d9b98a"></div></span><div>Lorem ipsum testing tincidu lorem dolor sit amet, elit dolor sitsitnt posuere..<small>Mara Ellison &nbsp; March 17, 2014</small></div></li>
      <li><span class="thumb"><div role="img" aria-label="Avatar" style="background:#d9b98a"></div></span><div>Lorem ipsum testing tincidu lorem dolor sit amet, elit dolor sitsitnt posuere..<small>Mara Ellison &nbsp; March 17, 2014</small></div></li>
    </ul>
    <p class="more">Read All →</p>
  </section>
</aside>

<footer class="abs footer">
  <span class="copy">All Right Reserved Copyright © 2014 &nbsp;- Terms and Conditions</span>
  <div class="social"><span></span><span></span><span></span><span></span></div>
</footer>
</body>
</html>
```